Tiny Meadow Product Label for Tear-Free Head-to-Toe Wash

Need a bottle label design for a new line of natural products targeting infants and children. Products are Pediatrician-developed and paraben-free, sulfate-free, fragrance-free, and cruelty-free. Design should be clean and have a high-end feel to it. Will need other product labels in Tiny Meadow line designed as well in upcoming projects.

Target Market(s)

Newborn to young elementary age children and their parents

Industry/Entity Type

Cosmetics/Beauty

Font styles to use
Other font styles liked:
• Brand fonts are Jost and Sonorous

Colors

Designer to choose colors to be used in the design.

Requirements
Must have
• Tiny Meadow logo, Pediatrician Developed logo, and a clean high-end feel to it. The label must fit the specialty bottle we will be using (label measurements and diagram will be provided) for the front and back of bottle only (NOT the side labels). It must include our list of ingredients (will provide once designer selected).
Nice to have
• Should stand out on the shelf of other baby products due to it's clean simplicity and high-end feel
Should not have
• too much of a "kiddie" feel to it (targeting the parents not the kids)

```html
<!DOCTYPE html>
<html lang="en">
<head>
<meta charset="utf-8">
<title>Tiny Meadow – Soothing Baby Lotion Label</title>
<link rel="stylesheet" href="https://fonts.googleapis.com/css2?family=Fredoka:wght@600&family=Jost:wght@400;500&display=swap">
<style>
  :root {
    --page: #ffffff;
    --label: #f7f1eb;
    --sage: #7a8580;
    --gold: #8d7252;
    --ink: #474747;
    --mark: #3c3c3c;
  }
  html, body {
    margin: 0;
    width: 1200px;
    height: 1200px;
    overflow: hidden;
    background: var(--page);
  }
  .canvas {
    width: 1200px;
    height: 1200px;
    display: flex;
    align-items: center;
    justify-content: center;
  }
  .label {
    width: 600px;
    height: 880px;
    background: var(--label);
    border-radius: 90px 90px 30px 30px;
    display: flex;
    flex-direction: column;
    align-items: center;
    box-sizing: border-box;
    padding-top: 80px;
    font-family: "Jost", sans-serif;
    text-align: center;
  }
  .brand-mark {
    display: flex;
    align-items: center;
    gap: 12px;
    height: 130px;
  }
  .brand-mark__circle {
    width: 40px;
    height: 40px;
    border: 2px solid var(--mark);
    border-radius: 50%;
    box-sizing: border-box;
  }
  .brand-mark__name {
    font-family: "Jost", sans-serif;
    font-weight: 500;
    font-size: 22px;
    letter-spacing: 3px;
    color: var(--mark);
    text-transform: uppercase;
  }
  .product-name {
    margin: 24px 0 0;
    font-family: "Fredoka", sans-serif;
    font-weight: 600;
    font-size: 118px;
    line-height: 0.98;
    color: var(--sage);
    letter-spacing: 1px;
  }
  .claim {
    margin-top: 14px;
    font-size: 27px;
    font-weight: 400;
    color: var(--gold);
    letter-spacing: 0.5px;
  }
  .product-type {
    margin-top: 52px;
    font-size: 39px;
    font-weight: 400;
    line-height: 1.15;
    letter-spacing: 2px;
    color: var(--sage);
  }
  .free-from {
    margin-top: 50px;
    font-size: 23px;
    font-weight: 400;
    line-height: 1.3;
    color: var(--ink);
  }
  .volume {
    margin-top: auto;
    margin-bottom: 70px;
    font-size: 29px;
    font-weight: 400;
    color: var(--ink);
    letter-spacing: 0.5px;
  }
</style>
</head>
<body>
<main class="canvas">
  <section class="label">
    <div class="brand-mark">
      <span class="brand-mark__circle"></span>
      <span class="brand-mark__name">Tiny Meadow</span>
    </div>
    <h1 class="product-name">TINY<br>MEADOW</h1>
    <div class="claim">PEDIATRICIAN DEVELOPED</div>
    <div class="product-type">SOOTHING<br>BABY LOTION</div>
    <div class="free-from">PARABEN-FREE - SULFATE-FREE<br>FRAGRANCE-FREE- CRUELTY-FREE</div>
    <div class="volume">8 FL OZ/237 ml</div>
  </section>
</main>
</body>
</html>
```